Business Cards for new orthopaedic surgery practice

My husband and I are starting our own orthopaedic surgery practice. We are looking for a business card that is uniform, but one will have my name/title and the other will have his. You can just create one design with my name on it for now. But when I choose your design as the winning design I will ask that you add another copy with his name/title.

We are looking for classy, simple, elite all in one. We like dark blues/a little gold/yellow. Something that goes with our logo. We want our logo incorporated. Here is all the info you need:
Business name: RV Bone & Vitality Center
Location: 38517 North Willowmere Ave
Palm Hollow, FL 33490
Phone: 954-218-4063
Fax: 954-582-7341
Email: info@myrvbonecare.example

Names: Lydia Vance, M.D.
Board Certified Hand and Upper Extremity Surgeon

Ebo Dansu, M.D.
Board Certified Hip & Knee Replacement/General Orthopaedic Surgeon

Can decide what you want to put on the back. Maybe a slogan:
Grounded in Care. Centered on You

I am just going to upload our logo. The only thing is if we select you as the winning design, the location, and phone numbers may change. We will need your help to update that once fully solidified.

Industry/Entity Type

Medical

Contact Information for Business Card

Colors
0054AA
0677BA
7BADD7
CADEEF
E8F1F8
0094D4
00A9DD
6FCCEA
C7EBF8
E9F6FB

Requirements
Must have
• class, appeal,
Should not have
• We want to air on the side of masculine if we are looking at masculine vs. feminine feel. But we still want it classy, sophisticated, and something we will love

```html
<!DOCTYPE html>
<html lang="en">
<head>
<meta charset="utf-8">
<title>RV Bone &amp; Vitality Center — Business Cards</title>
<link href="https://fonts.googleapis.com/css2?family=Montserrat:wght@400;500;700&display=swap" rel="stylesheet">
<style>
  :root {
    --backdrop: #2e2e30;
    --navy: #1c2b52;
    --gold: #c9a45c;
    --white: #ffffff;
    --soft-white: #e9ecf3;
  }
  * { box-sizing: border-box; margin: 0; padding: 0; }
  html, body {
    width: 1200px; height: 875px; overflow: hidden;
    background: var(--backdrop);
    font-family: "Montserrat", Arial, sans-serif;
  }
  .sheet {
    width: 1200px; height: 875px;
    display: flex; flex-direction: column; align-items: center; justify-content: center;
    gap: 40px;
  }
  .card {
    position: relative;
    width: 660px; height: 377px;
    background: var(--navy);
    border-radius: 18px;
    overflow: hidden;
    color: var(--white);
  }
  .brand {
    display: flex; flex-direction: column; align-items: center; gap: 10px;
  }
  .brand-mark {
    width: 22px; height: 22px; border-radius: 50%;
    border: 2px solid var(--gold);
  }
  .brand-name {
    font-weight: 500; letter-spacing: 0.18em; text-transform: uppercase;
    color: var(--white); text-align: center; line-height: 1.35; white-space: nowrap;
  }
  /* Front */
  .card-front .brand {
    position: absolute; left: 0; right: 0; top: 110px;
  }
  .card-front .brand-name { font-size: 20px; }
  .tagline {
    position: absolute; left: 0; right: 0; top: 260px;
    text-align: center; font-size: 17px; font-weight: 400; color: var(--soft-white);
    letter-spacing: 0.02em;
  }
  /* Back */
  .card-back .brand {
    position: absolute; right: 36px; top: 40px;
  }
  .card-back .brand-name { font-size: 12px; }
  .person {
    position: absolute; left: 44px; top: 176px;
  }
  .person-name {
    font-size: 22px; font-weight: 700; color: var(--gold); letter-spacing: 0.01em;
  }
  .person-title {
    font-size: 13px; font-weight: 400; color: var(--soft-white); margin-top: 4px;
  }
  .divider {
    position: absolute; left: 44px; right: 40px; top: 240px;
    height: 1px; background: var(--gold); opacity: 0.8;
  }
  .contact-list {
    position: absolute; left: 44px; top: 258px;
    list-style: none; font-size: 13px; color: var(--soft-white);
  }
  .contact-list li { display: flex; align-items: center; gap: 10px; height: 22px; }
  .contact-list svg { width: 12px; height: 12px; fill: var(--gold); flex: none; }
  .address {
    position: absolute; right: 40px; top: 264px;
    font-style: normal; font-size: 13px; line-height: 1.6; color: var(--soft-white); text-align: right;
  }
  .gold-band {
    position: absolute; left: 0; right: 0; bottom: 0; height: 12px; background: var(--gold);
  }
</style>
</head>
<body>
<main class="sheet">

  <section class="card card-front" aria-label="Business card front">
    <div class="brand">
      <span class="brand-mark"></span>
      <span class="brand-name">RV Bone &amp; Vitality Center</span>
    </div>
    <p class="tagline">Grounded in Care. Centered on You</p>
  </section>

  <section class="card card-back" aria-label="Business card back">
    <div class="brand">
      <span class="brand-mark"></span>
      <span class="brand-name">RV Bone &amp; Vitality Center</span>
    </div>

    <div class="person">
      <h1 class="person-name">LYDIA VANCE, M.D.</h1>
      <p class="person-title">Board Certified Hand and Upper Extremity Surgeon</p>
    </div>

    <div class="divider"></div>

    <ul class="contact-list">
      <li>
        <svg viewBox="0 0 24 24" aria-hidden="true"><path d="M6.6 10.8a15.1 15.1 0 0 0 6.6 6.6l2.2-2.2a1 1 0 0 1 1-.25 11.4 11.4 0 0 0 3.6.57 1 1 0 0 1 1 1V20a1 1 0 0 1-1 1A17 17 0 0 1 3 4a1 1 0 0 1 1-1h3.5a1 1 0 0 1 1 1c0 1.25.2 2.450.57 3.57a1 1 0 0 1-.25 1z"/></svg>
        954-218-4063
      </li>
      <li>
        <svg viewBox="0 0 24 24" aria-hidden="true"><path d="M6 2h12v6H6zM3 9h18a1 1 0 0 1 1 1v7h-4v5H6v-5H2v-7a1 1 0 0 1 1-1zm5 8v3h8v-3z"/></svg>
        954-582-7341
      </li>
      <li>
        <svg viewBox="0 0 24 24" aria-hidden="true"><path d="M2 5h20v14H2zm2 2v.5l8 5 8-5V7l-8 5z"/></svg>
        info@myrvbonecare.example
      </li>
    </ul>

    <address class="address">
      38517 North Willowmere Ave<br>
      Palm Hollow, FL 33490
    </address>

    <div class="gold-band"></div>
  </section>

</main>
</body>
</html>
```